We need a laundry sheet packingbox desgin

-look at our website lindavel.nl to be in line with our house style/collor
We are a perfume seller and would like to offer also wasshingsheets with NO SMELL, so the customers can buy this incombination with our washingperfumes.
-the wassingheets will be neutrale(NO SMELL)
-it will be for the Dutch market
The next points should be on the desgin of the package
-our brand name: LINDAVEL
-product name: WASSTRIPS
-(contains) Bevat: 30 wasstrips
-30 wasstrips = 60 wasbeurten
Please take some inspiration of others sellers & regarding eco friendly symbols etc.:
voltirra.com & plomkens.nl
Backside information will be provided afther we found the right desgin
Please look at attachement pdf open box.
Here you can find the pdf design where you need to customize:
https://fz.qx/t-kR8bNwL2sY

```html
<!DOCTYPE html>
<html lang="nl">
<head>
<meta charset="utf-8">
<title>LINDAVEL Wasstrips – verpakking voorzijde</title>
<link href="https://fonts.googleapis.com/css2?family=Playfair+Display:wght@400;700;900&family=Poppins:wght@400;600;700&display=swap" rel="stylesheet">
<style>
  :root{
    --backdrop:#8a8a8a;
    --paper:#f4f3f1;
    --paper-shade:#e6e5e2;
    --gold-deep:#bf8a2e;
    --gold-mid:#cc9f40;
    --gold-light:#d9b24c;
    --gold-text:#b98a2c;
    --white:#ffffff;
  }
  *{margin:0;padding:0;box-sizing:border-box}
  html,body{width:840px;height:1200px;overflow:hidden;background:var(--backdrop)}
  .canvas{position:relative;width:840px;height:1200px}
  .box-front{position:absolute;left:60px;top:80px;width:720px;height:1040px;overflow:hidden;background:var(--paper)}
  .box-front__art{position:absolute;inset:0}
  .brand{position:absolute;left:0;right:0;top:205px;text-align:center;
    font-family:"Playfair Display",serif;font-weight:400;font-size:34px;letter-spacing:3px;color:var(--gold-text)}
  .brand__dot{display:block;width:70px;height:70px;margin:0 auto 26px;border-radius:50%;background:var(--gold-light)}
  .product-name{position:absolute;left:0;right:0;top:510px;text-align:center;
    font-family:"Playfair Display",serif;font-weight:900;font-size:104px;line-height:1;letter-spacing:-2px;color:var(--white);white-space:nowrap}
  .claims{position:absolute;left:62px;top:650px;font-family:"Poppins",sans-serif;font-size:24px;line-height:1.38;color:var(--white)}
  .claims strong{font-weight:700}
  .usage-steps{position:absolute;left:62px;top:770px;width:600px;height:140px}
  .stats{position:absolute;left:0;right:0;top:940px;height:70px}
  .stat{position:absolute;display:flex;align-items:center;gap:10px;font-family:"Poppins",sans-serif;color:var(--white)}
  .stat__num{font-size:30px;font-weight:600;line-height:1}
  .stat__label{font-size:14px;line-height:1.2}
  .stat__text{display:flex;flex-direction:column}
  .stat--strips{left:250px;top:8px}
  .stat--washes{left:420px;top:0}
  .rule{position:absolute;height:1.5px;background:var(--white)}
  .rule--left{left:0;top:1010px;width:140px}
  .rule--right{right:0;top:955px;width:120px}
</style>
</head>
<body>
<div class="canvas">
  <section class="box-front">
    <svg class="box-front__art" width="720" height="1040" viewBox="0 0 720 1040" role="img" aria-label="Witte bovenzijde en goudkleurige onderzijde met een fijn bladerpatroon">
      <defs>
        <linearGradient id="goldFill" x1="0" y1="0" x2="1" y2="0.3">
          <stop offset="0" stop-color="var(--gold-deep)"/>
          <stop offset="0.6" stop-color="var(--gold-mid)"/>
          <stop offset="1" stop-color="var(--gold-light)"/>
        </linearGradient>
        <linearGradient id="paperFill" x1="0" y1="0" x2="1" y2="1">
          <stop offset="0" stop-color="var(--white)"/>
          <stop offset="1" stop-color="var(--paper-shade)"/>
        </linearGradient>
      </defs>
      <rect width="720" height="1040" fill="url(#paperFill)"/>
      <path d="M0,0 C40,230 180,360 370,400 C520,430 660,500 720,690 L720,1040 L0,1040 Z" fill="url(#goldFill)"/>
      <path d="M12,0 C52,220 192,345 378,384 C530,415 668,488 720,660" fill="none" stroke="var(--gold-light)" stroke-width="3"/>
    </svg>

    <div class="brand"><span class="brand__dot"></span>LINDAVEL</div>

    <h1 class="product-name">WASSTRIPS</h1>

    <p class="claims">
      <strong>Bevat: 30 wasstrips</strong> = 60 wasbeurten<br>
      100% <strong>Milieuvriendelijk</strong><br>
      <strong>Geurloos</strong> – neutraal, zonder parfum
    </p>

    <svg class="usage-steps" viewBox="0 0 600 140">
      <rect x="0" y="0" width="150" height="140" rx="8" fill="var(--white)" fill-opacity="0.12" role="img" aria-label="Shirt met vlekken plus een wasstrip"/>
      <path d="M170,80 C200,60 225,95 250,78" fill="none" stroke="var(--white)" stroke-width="2"/>
      <path d="M244,72 L252,78 L243,84" fill="none" stroke="var(--white)" stroke-width="2"/>
      <rect x="270" y="10" width="150" height="125" rx="8" fill="var(--white)" fill-opacity="0.12" role="img" aria-label="Wasmachine"/>
      <path d="M430,80 C455,62 475,95 505,70" fill="none" stroke="var(--white)" stroke-width="2"/>
      <path d="M498,66 L507,70 L500,78" fill="none" stroke="var(--white)" stroke-width="2"/>
      <rect x="515" y="0" width="85" height="110" rx="8" fill="var(--white)" fill-opacity="0.12" role="img" aria-label="Schoon glanzend shirt"/>
    </svg>

    <div class="stats">
      <div class="stat stat--strips">
        <svg width="50" height="46" viewBox="0 0 50 46"><path d="M16,2 L48,2 L34,44 L2,44 Z" fill="var(--white)"/></svg>
        <div class="stat__text"><span class="stat__num">30</span><span class="stat__label">wasstrips</span></div>
      </div>
      <div class="stat stat--washes">
        <svg width="54" height="54" viewBox="0 0 54 54"><rect x="2" y="2" width="50" height="50" rx="8" fill="none" stroke="var(--white)" stroke-width="2.5"/><circle cx="27" cy="29" r="14" fill="none" stroke="var(--white)" stroke-width="2.5"/><path d="M15,31 C22,36 30,26 39,31 A14,14 0 0 1 15,31 Z" fill="var(--white)"/></svg>
        <div class="stat__text"><span class="stat__num">60</span><span class="stat__label">wasbeurten</span></div>
      </div>
    </div>
    <div class="rule rule--left"></div>
    <div class="rule rule--right"></div>
  </section>
</div>
</body>
</html>
```